Podiatry clinic requires a modern revamp and editing of existing website.

I would like a fresh new look and updated information for my current business website. An easy to navigate site with prominent address and phone number for call to action. We are a podiatry clinic that focuses on general and sports podiatry.
I would like 4 pages; including Home page, About Us, Services & Contact.
www.brambleridgepodiatry.net

Target Market(s)

Active working professionals.

Industry/Entity Type

Medical

Coding

Coded - Design and coding required

Number of Pages Required

4 page

Font styles to use
Sans Serif

Colors
6b449b

Requirements
Must have
• A modern look with logo and active images; clean and uncluttered. Visible phone number and address for call to action.
• 4 pages - Home, About Us, Services, Contact.
• Home page - update address & service logos.
• About Us - update of personal information.
• Services - Revamp of existing page.
• Contact page to include Google map, email & phone number.
Nice to have
• Ability to add content easily; eg. a blog or adding video onto Home page.
• Link to Friendsphere page.

```html
<!DOCTYPE html>
<html lang="en">
<head>
<meta charset="utf-8">
<title>Brambleridge Podiatry</title>
<link href="https://fonts.googleapis.com/css2?family=Open+Sans:wght@400;600;700;800&display=swap" rel="stylesheet">
<style>
:root{
  --purple:#6b449b;
  --purple-dark:#4f2f78;
  --purple-light:#8a66b8;
  --orange:#f7941d;
  --text:#555;
  --grey-bg:#efeef2;
  --white:#fff;
}
*{box-sizing:border-box;margin:0;padding:0}
html,body{width:1200px;height:2216px;overflow:hidden}
body{font-family:"Open Sans",Arial,sans-serif;color:var(--text);background:var(--white);position:relative}
.brand{display:flex;align-items:center;gap:14px;font-weight:800;font-size:30px;line-height:1.05;color:var(--purple)}
.brand-dot{width:46px;height:46px;border-radius:50%;background:var(--orange);flex:none}
.site-header{position:absolute;left:96px;top:40px;width:1008px;height:120px}
.site-header .brand{position:absolute;left:0;top:14px;width:260px}
.header-info{position:absolute;right:0;top:0;text-align:right;font-size:14px;color:var(--purple)}
.follow{font-size:13px;color:#777;margin-bottom:12px}
.follow b{color:var(--purple);font-size:17px;margin-left:6px}
.header-row{display:flex;gap:26px;align-items:center;justify-content:flex-end}
.address{font-weight:600;line-height:1.35;text-align:left}
.phone{display:flex;align-items:center;gap:8px;font-size:22px;font-weight:700}
.main-nav{position:absolute;left:360px;top:172px;display:flex}
.main-nav a{display:block;padding:0 26px;height:30px;line-height:30px;font-size:13px;font-weight:700;color:var(--white);background:var(--purple);text-decoration:none}
.main-nav a.active{background:var(--purple-dark)}
.hero{position:absolute;left:96px;top:202px;width:1008px;height:478px;background:linear-gradient(110deg,#d9d4cf 0%,#a79a91 35%,#5c4f4a 70%,#3a3138 100%)}
.hero-intro{position:absolute;right:60px;top:150px;width:380px;color:var(--white)}
.hero-intro h1{font-size:24px;font-weight:700;margin-bottom:12px}
.hero-intro p{font-size:13px;line-height:1.6;margin-bottom:24px}
.btn{display:inline-block;background:var(--purple);color:var(--white);font-size:12px;font-weight:700;padding:9px 22px;text-decoration:none;letter-spacing:.5px}
.btn+.btn{margin-left:14px}
.slider-arrow{position:absolute;top:215px;width:34px;height:44px;background:var(--purple);display:flex;align-items:center;justify-content:center}
.slider-arrow.prev{left:0}.slider-arrow.next{right:0}
.cards{position:absolute;left:160px;top:712px;width:900px;display:flex;gap:40px}
.card{width:430px;position:relative}
.card-photo{height:200px;margin-left:60px;background:linear-gradient(135deg,#e9dcd2,#b99d8c)}
.card-badge{position:absolute;left:0;top:-10px;width:118px;height:118px;border-radius:50%;background:var(--orange);border:5px solid var(--white);color:var(--white);font-weight:700;font-size:17px;display:flex;align-items:center;justify-content:center;text-align:center;line-height:1.2}
.card p{font-size:12.5px;line-height:1.6;margin:26px 10px 22px}
.card .btn{display:block;width:150px;margin:0 auto;text-align:center}
.about-band{position:absolute;left:0;top:1220px;width:1200px;height:360px;background:var(--purple)}
.about-badge{position:absolute;left:130px;top:75px;width:210px;height:210px;border-radius:50%;background:var(--orange);border:6px solid var(--white);color:var(--white);display:flex;flex-direction:column;justify-content:center;align-items:center;text-align:center}
.about-badge span{font-size:24px}
.about-badge strong{font-size:23px;line-height:1.15;font-weight:800}
.about-text{position:absolute;left:385px;top:62px;width:640px;color:var(--white);font-size:13px;line-height:1.65}
.about-text p{margin-bottom:14px}
.about-text .btn{background:var(--purple-light)}
.partners{position:absolute;left:160px;top:1620px;width:880px;height:130px;display:flex;align-items:center;justify-content:space-between}
.partners .brand{font-size:22px;width:210px}
.partner{width:130px;height:54px;border-radius:6px;background:#dcd7e4}
.site-footer{position:absolute;left:0;top:1820px;width:1200px;height:340px;background:var(--grey-bg)}
.site-footer .brand{position:absolute;left:110px;top:46px;width:200px;font-size:24px}
.footer-col{position:absolute;top:40px;font-size:13px;line-height:1.85}
.footer-col h3{font-size:14px;color:var(--purple);font-weight:700;border-bottom:1px solid #ccc;padding-bottom:6px;margin-bottom:10px;width:150px}
.col-links{left:360px}.col-contact{left:540px}
.col-contact b{color:var(--purple);margin-left:4px}
.map{position:absolute;left:760px;top:50px;width:330px;height:230px;background:linear-gradient(135deg,#e6e3da,#cfd8c9)}
.copyright{position:absolute;left:0;top:2160px;width:1200px;height:56px;background:var(--purple);color:var(--white);font-size:11px;font-weight:600;text-align:center;line-height:56px;letter-spacing:.5px}
</style>
</head>
<body>
<header class="site-header">
  <div class="brand"><span class="brand-dot"></span><span>Brambleridge Podiatry</span></div>
  <div class="header-info">
    <div class="follow">Follow us on <b>Friendsphere</b></div>
    <div class="header-row">
      <div class="address">Suite 27<br>118 Harrow Lane<br>Fenwick 4102</div>
      <div class="phone">
        <svg width="22" height="22" viewBox="0 0 24 24"><path fill="#6b449b" d="M6.6 10.8a15 15 0 006.6 6.6l2.2-2.2a1 1 0 011-.25 11.4 11.4 0 003.6.57 1 1 0 011 1V20a1 1 0 01-1 1A17 17 0 013 4a1 1 0 011-1h3.5a1 1 0 011 1c0 1.25.2 2.45.57 3.57a1 1 0 01-.25 1z"/></svg>
        1300 482 905
      </div>
    </div>
  </div>
</header>

<nav class="main-nav">
  <a class="active" href="#">HOME</a><a href="#">ABOUT US</a><a href="#">SERVICES</a><a href="#">CONTACT</a>
</nav>

<section class="hero" role="img" aria-label="Runner's foot in a sports shoe with glowing joints highlighted">
  <span class="slider-arrow prev"><svg width="14" height="20" viewBox="0 0 14 20"><path d="M11 2L3 10l8 8" stroke="#fff" stroke-width="3" fill="none"/></svg></span>
  <span class="slider-arrow next"><svg width="14" height="20" viewBox="0 0 14 20"><path d="M3 2l8 8-8 8" stroke="#fff" stroke-width="3" fill="none"/></svg></span>
  <div class="hero-intro">
    <h1>Welcome to Brambleridge Podiatry</h1>
    <p>We provide General Podiatry Treatment and some Specialised Services in relation to various foot conditions, including Sports Injuries, Orthotic Therapy and Nail Surgery.</p>
    <a class="btn" href="#">VIEW SERVICES</a><a class="btn" href="#">MAKE AN APPOINTMENT</a>
  </div>
</section>

<section class="cards">
  <article class="card">
    <div class="card-photo" role="img" aria-label="Podiatrist examining a patient's foot"></div>
    <div class="card-badge">General<br>Treatments</div>
    <p>At Brambleridge Podiatry, we provide general treatments including nails, corns, calluses, warts, skin disorders, heel pain, foot sprains, arch pain, ankle pain, shin splints, knee pain, bunions and toe deformities.</p>
    <a class="btn" href="#">LEARN MORE</a>
  </article>
  <article class="card">
    <div class="card-photo" role="img" aria-label="Hands massaging a patient's foot"></div>
    <div class="card-badge">Specialised<br>Treatments</div>
    <p>Our specialised treatments include diabetic management, nail surgery, biomechanical assessment, gait analysis, orthotic therapy and sports injury care for active people.</p>
    <a class="btn" href="#">LEARN MORE</a>
  </article>
</section>

<section class="about-band">
  <div class="about-badge"><span>About</span><strong>Brambleridge<br>Podiatry</strong></div>
  <div class="about-text">
    <p>Brambleridge Podiatry is a podiatry clinic in the heart of Fenwick. We are located between Harrow and Linden Lanes in the Riverside Business Centre.</p>
    <p>Our podiatrists are fully qualified health professionals who are able to diagnose, treat, manage or help to prevent all medical conditions that affect the feet and lower limbs.</p>
    <p>We provide General Podiatry Treatment and some Specialised Services in relation to various foot conditions, including Sports Injuries, Orthotic Therapy and Nail Surgery.</p>
    <p>For Appointments or Enquiries please call us on 1300 482 905 or email hello@brambleridgepodiatry.net</p>
    <a class="btn" href="#">MORE ABOUT US</a>
  </div>
</section>

<section class="partners">
  <div class="brand"><span class="brand-dot"></span><span>Brambleridge Podiatry</span></div>
  <span class="partner"></span><span class="partner"></span><span class="partner"></span><span class="partner"></span>
</section>

<footer class="site-footer">
  <div class="brand"><span class="brand-dot"></span><span>Brambleridge Podiatry</span></div>
  <div class="footer-col col-links">
    <h3>QUICK LINKS</h3>
    Home<br>About Us<br>Services<br>Contact
  </div>
  <div class="footer-col col-contact">
    <h3>CONTACT</h3>
    Brambleridge Podiatry<br>Suite 27<br>118 Harrow Lane<br>Fenwick 4102<br>1300 482 905<br>hello@brambleridgepodiatry.net<br>Follow us on <b>Friendsphere</b>
  </div>
  <div class="map" role="img" aria-label="Street map showing the clinic location"></div>
</footer>
<div class="copyright">COPYRIGHT &copy; BRAMBLERIDGE PODIATRY. ALL RIGHTS RESERVED.</div>
</body>
</html>
```